Velvet Meadow Hamper company needs a brochure design

We need a brochure design for a new company in Dubai called 'Velvet Meadow Hampers'. We already have a logo designed which I have attached and would like to use this and the green/gold/white colours for our brochure. Our company initially will be supplying Velvet Meadow Hamper wear of traditional wicker baskets in many designs which hold all the cutlery, crockery and accessories. We will also be selling picnic accessories. We want to purvey a sense of luxury and class in line with our logo. I have attached some photos of the picnicwear. As our products are changing all the time I thought a fold out cover which stays the same and then product cards inserted into the folder which can be changed according to our product changes. I am looking for a fairly simple design and each product card should have at least one photo of the product on it with a spec and description also. On the cover of the folder I would like room to write about the company and what we do, this can be inside or out and may or may not include photos. I have the logo designs in illustrator format and pdf. Please contact if any more information is needed.
Updates

Reason: I have extended this deadline as there are some content changes taking place.

Industry/Entity Type

It Company

```html
<!DOCTYPE html>
<html lang="en">
<head>
<meta charset="utf-8">
<title>Velvet Meadow Hampers – Willowmere Product Card</title>
<link href="https://fonts.googleapis.com/css2?family=Arimo:wght@400;700&family=Tinos:wght@400&display=swap" rel="stylesheet">
<style>
  :root {
    --meadow-green: #1b3119;
    --meadow-green-deep: #172b16;
    --gold: #c9a13b;
    --gold-soft: #b8913a;
    --cream: #f3efe4;
    --paper: #ffffff;
    --band-brown: #6a2a1c;
  }
  html, body {
    margin: 0;
    padding: 0;
    width: 1200px;
    height: 1000px;
    overflow: hidden;
    background: var(--paper);
  }
  .canvas {
    position: relative;
    width: 1200px;
    height: 1000px;
    background: var(--paper);
  }
  .card {
    position: absolute;
    top: 150px;
    width: 493px;
    height: 700px;
    background: var(--meadow-green);
    overflow: hidden;
  }
  .card--front { left: 100px; }
  .card--spec { left: 607px; }

  /* Front card */
  .brand-header {
    position: absolute;
    left: 0; top: 0;
    width: 100%;
    height: 147px;
    background: var(--meadow-green);
  }
  .brand-name {
    position: absolute;
    top: 64px;
    width: 100%;
    text-align: center;
    font-family: "Arimo", Arial, sans-serif;
    font-weight: 700;
    font-size: 12.5px;
    letter-spacing: 2.6px;
    color: var(--gold);
    margin: 0;
  }
  .brand-dot {
    position: absolute;
    left: 240px;
    top: 44px;
    width: 12px;
    height: 12px;
    border-radius: 50%;
    background: var(--gold);
  }
  .gold-band {
    position: absolute;
    left: 0;
    width: 100%;
    height: 6px;
    background: linear-gradient(90deg, var(--band-brown) 0%, #8a4a24 30%, #d6a84c 65%, #fff6dc 78%, #d1a04a 88%, var(--band-brown) 100%);
  }
  .gold-band--top { top: 147px; }
  .gold-band--bottom {
    top: 513px;
    background: linear-gradient(90deg, #8a5a2a 0%, #c99a48 12%, #fff6dc 24%, #c28a3c 45%, #7a3420 75%, var(--band-brown) 100%);
  }
  .product-stage {
    position: absolute;
    left: 0;
    top: 153px;
    width: 100%;
    height: 360px;
    background: var(--paper);
  }
  .product-photo {
    position: absolute;
    left: 90px;
    top: 22px;
    width: 315px;
    height: 325px;
    border-radius: 4px;
    background: linear-gradient(160deg, #6e4a2c 0%, #9c7048 40%, #1f3424 55%, #a77b52 75%, #5a3a22 100%);
  }
  .product-title {
    position: absolute;
    left: 28px;
    top: 534px;
    margin: 0;
    font-family: "Arimo", Arial, sans-serif;
    font-weight: 700;
    font-size: 24px;
    letter-spacing: 2.4px;
    color: var(--gold);
  }
  .product-description {
    position: absolute;
    left: 28px;
    top: 571px;
    width: 412px;
    margin: 0;
    font-family: "Tinos", "Times New Roman", serif;
    font-size: 11px;
    line-height: 13.4px;
    color: var(--cream);
  }
  .site-address {
    position: absolute;
    bottom: 15px;
    width: 100%;
    text-align: center;
    font-family: "Tinos", "Times New Roman", serif;
    font-size: 11px;
    color: var(--gold);
    margin: 0;
  }

  /* Spec card */
  .divider {
    position: absolute;
    left: 180px;
    width: 133px;
    height: 1px;
    background: var(--gold-soft);
  }
  .divider--top { top: 192px; }
  .divider--bottom { top: 487px; }
  .flourish {
    position: absolute;
    left: 218px;
    width: 57px;
    height: 16px;
    background: var(--gold-soft);
    opacity: 0.55;
    border-radius: 8px;
  }
  .flourish--top { top: 172px; }
  .flourish--bottom { top: 492px; }
  .spec-title {
    position: absolute;
    top: 214px;
    width: 100%;
    margin: 0;
    text-align: center;
    font-family: "Arimo", Arial, sans-serif;
    font-weight: 700;
    font-size: 23px;
    letter-spacing: 3px;
    color: var(--gold);
  }
  .spec-subtitle {
    position: absolute;
    top: 243px;
    width: 100%;
    margin: 0;
    text-align: center;
    font-family: "Tinos", "Times New Roman", serif;
    font-size: 16px;
    color: var(--gold);
  }
  .spec-list {
    position: absolute;
    left: 126px;
    top: 281px;
    width: 300px;
    margin: 0;
    padding: 0;
    list-style: none;
    font-family: "Tinos", "Times New Roman", serif;
    font-size: 11px;
    line-height: 16.5px;
    color: var(--cream);
  }
  .spec-list li {
    position: relative;
    padding-left: 15px;
  }
  .spec-list li::before {
    content: "";
    position: absolute;
    left: 0;
    top: 6px;
    width: 5px;
    height: 5px;
    background: var(--gold);
  }
</style>
</head>
<body>
<main class="canvas">

  <section class="card card--front">
    <header class="brand-header">
      <span class="brand-dot"></span>
      <p class="brand-name">VELVET MEADOW HAMPERS</p>
    </header>
    <div class="gold-band gold-band--top"></div>
    <div class="product-stage">
      <div class="product-photo" role="img" aria-label="Photo of an open wicker picnic hamper for six with white plates, cutlery and green lining"></div>
    </div>
    <div class="gold-band gold-band--bottom"></div>
    <h1 class="product-title">WILLOWMERE, 6 Person</h1>
    <p class="product-description">This stylish picnic hamper contains everything you could possibly need for the most indulgent of outdoor dining experiences. The rich dark willow, brown leather handles and the dark green colour palette make for a sophisticated accessory to outdoor dining. The basket comes equipped for 6 with a range of accessories, including reinforced glass tumblers and a built in chiller compartment to keep food cold. A fantastic hamper for large families or a group of friends and will guarantee a great day out for all!</p>
    <p class="site-address">www.velvetmeadowhampers.com</p>
  </section>

  <section class="card card--spec">
    <div class="flourish flourish--top" role="img" aria-label="Gold decorative flourish"></div>
    <div class="divider divider--top"></div>
    <h2 class="spec-title">WILLOWMERE, 6 Person</h2>
    <p class="spec-subtitle">OVERVIEW</p>
    <ul class="spec-list">
      <li>Handmade dark willow basket for six people</li>
      <li>Brown leather straps and trim</li>
      <li>Built in chiller compartment</li>
      <li>Dark green colour palette</li>
      <li>6 White china plates</li>
      <li>6 Stainless steel, knifes, forks and spoons</li>
      <li>Stainless steel salt and pepper mills</li>
      <li>1 wooden chopping board</li>
      <li>6 reinforced glass tumblers held in a willow basket, 200 x 170 x 100mm</li>
      <li>Dimensions 540 x 340 x 200mm</li>
    </ul>
    <div class="divider divider--bottom"></div>
    <div class="flourish flourish--bottom" role="img" aria-label="Gold decorative flourish"></div>
    <p class="site-address">www.velvetmeadowhampers.com</p>
  </section>

</main>
</body>
</html>
```